Floravine Pte Ltd

I want a creative and stand out web page so when my client search for my web page or google search. The front page is stand out and they know that we are the interior office designer that are searching for . We are commercial office design company. We also have the video to put at our front page for client to see. Natural is the key elements. As we like to carry recycle materials , plant , trees is our key element such as biophilic design
Updates

Hi All,

For my web page, I need minimalist design and creative frontpage.
When my client search for my web page, they straight feel that this is the office design company.
The webpage is special and nature is the key element for the design.
My company logo can be design in the shaped of the letter OO in the webpage.
Below is the sample you can refer.

https://www.pinboardly.example/pin/527190364821057392/

Target Market(s)

Customer searching for office design

Industry/Entity Type

Commerical designer firm- Office interior design & Build company

Number of Pages Required

5+ page

Font styles to use
Other font styles liked:
• Wilmina

Colors
59FF00
82FF00
B8FF75
E3FFCB
F4FFEA
FFC000
F8CF3A
FAE287
FDF2CF
FEFAEE
6B429C
8869AF
B7A5CE
E3DAEB
F3F0F8

Requirements
Must have
• Home, Services,Gallery, Calculator, Testimonials, Contact, Blog
Nice to have
• Natural, creative, minimalist
Should not have
• No black color or blue color

```html
<!DOCTYPE html>
<html lang="en">
<head>
<meta charset="utf-8">
<title>Floravine Pte Ltd — Interior designer</title>
<link href="https://fonts.googleapis.com/css2?family=Kumbh+Sans:wght@300;400;500;600&display=swap" rel="stylesheet">
<style>
:root{
  --purple:#6B429C;
  --purple-soft:#8869AF;
  --purple-pale:#E3DAEB;
  --yellow:#FFC000;
  --yellow-warm:#F8CF3A;
  --ink:#2a2230;
  --text:#3b3440;
  --muted:#8d8794;
  --brand:#ee4422;
  --band:#f3f3f4;
  --white:#ffffff;
}
*{margin:0;padding:0;box-sizing:border-box}
html,body{width:1200px;height:3787px;overflow:hidden;background:var(--white)}
body{font-family:"Kumbh Sans",sans-serif;color:var(--text);position:relative}
.abs{position:absolute}
a{color:inherit;text-decoration:none}

/* header */
.brand{display:flex;align-items:center;gap:8px;color:var(--brand);font-weight:400}
.brand .dot{width:18px;height:18px;border:3px solid var(--brand);border-radius:50%}
.header-brand{left:110px;top:28px;font-size:19px}
.badge{background:#f5e6e2;border-radius:3px}
.header-badge{left:202px;top:58px;width:36px;height:16px}
.nav{top:36px;left:385px;display:flex;gap:23px;font-size:13px;color:var(--ink)}
.login{left:1005px;top:30px;display:flex;align-items:center;gap:10px;font-size:14px;color:var(--ink)}
.login .ico{width:36px;height:36px;border-radius:50%;background:var(--purple);display:flex;align-items:center;justify-content:center}

/* hero */
.photo{border-radius:0}
.hero-left{left:0;top:115px;width:175px;height:498px;background:linear-gradient(180deg,#d9d6d1 0%,#bfb8ae 45%,#a59c8f 100%)}
.hero-right{left:468px;top:235px;width:683px;height:465px;background:linear-gradient(90deg,#e9e6ea 0%,#bdb7bd 22%,#2c2a2e 38%,#3a383b 60%,#6f6a63 85%,#9c958b 100%)}
.hero-kicker{left:268px;top:138px;font-size:21px;color:var(--purple)}
.hero-title{left:262px;top:178px;font-size:96px;font-weight:500;line-height:98px;color:var(--ink);letter-spacing:-1px}
.side-line{left:233px;top:147px;width:1px;height:125px;background:var(--muted)}
.side-label{left:226px;top:378px;font-size:12px;color:var(--ink);transform:rotate(-90deg);transform-origin:left top;letter-spacing:.5px}
.btn{background:var(--yellow);color:var(--ink);border-radius:26px;display:flex;align-items:center;justify-content:center;font-size:15px;font-weight:500}
.hero-btn{left:266px;top:389px;width:160px;height:52px}
.play{left:234px;top:604px;display:flex;align-items:center;gap:16px;font-size:12px;color:var(--purple)}
.play .circle{width:48px;height:48px;border-radius:50%;background:var(--purple);box-shadow:0 0 0 4px var(--purple-pale);display:flex;align-items:center;justify-content:center}

/* partners */
.partners{left:0;top:750px;width:1200px;height:90px}
.arrow{color:var(--purple);font-size:22px}
.partner{background:#ececec;border-radius:8px}

/* about */
.about-back{left:238px;top:982px;width:308px;height:427px;background:linear-gradient(180deg,#eef0f2 0%,#cfd5da 40%,#9fa3a6 70%,#cbcac7 100%)}
.about-front{left:116px;top:929px;width:210px;height:287px;background:var(--white);padding:7px;box-shadow:0 10px 30px rgba(60,40,80,.18)}
.about-front div{width:100%;height:100%;background:linear-gradient(180deg,#6a655f 0%,#3b3733 45%,#8f7b63 100%)}
.about-title{left:609px;top:993px;font-size:40px;font-weight:400;color:var(--ink)}
.about-text{left:609px;top:1057px;width:470px;font-size:15px;line-height:30px;color:var(--text)}
.about-btn{left:607px;top:1326px;width:160px;height:52px}

/* gallery */
.gallery-band{left:0;top:1531px;width:1200px;height:704px;background:var(--band)}
.section-title{width:1200px;left:0;text-align:center;font-size:38px;color:var(--ink);font-weight:400}
.tile{overflow:hidden}
.tile-overlay{background:linear-gradient(180deg,#7d56b2,#6B429C);display:flex;align-items:center;justify-content:center;text-align:center;color:var(--white);font-size:23px;line-height:36px}

/* promo */
.promo-bg{left:413px;top:2301px;width:787px;height:568px;background:linear-gradient(135deg,#f8cf3a 0%,#ffc000 55%,#e9b10a 100%)}
.promo-text{left:666px;top:2408px;width:520px;font-size:38px;line-height:63px;color:var(--ink)}
.promo-link{left:670px;top:2750px;font-size:19px;color:var(--purple);text-decoration:underline}

/* awards */
.award{background:var(--white);box-shadow:0 8px 30px rgba(0,0,0,.07);display:flex;align-items:center;justify-content:center}
.award .mark{width:150px;height:90px;border-radius:45px;background:#ececec}
.award.gold .mark{background:#f3e7c6}

/* footer */
.footer-brand{left:490px;top:3398px;font-size:32px}
.footer-brand .dot{width:40px;height:40px;border-width:5px}
.footer-badge{left:654px;top:3462px;width:64px;height:28px}
.footer-nav{top:3560px;left:0;width:1200px;display:flex;justify-content:center;gap:23px;font-size:13px;color:var(--ink)}
.copy{top:3615px;left:0;width:1200px;text-align:center;font-size:13px;color:var(--ink)}
.copy span{color:var(--purple);text-decoration:underline}
.social{width:44px;height:44px;border-radius:50%;background:var(--purple-pale)}
.social.on{background:var(--yellow)}
.chat{left:1114px;top:3377px;width:46px;height:46px;border-radius:50%;background:var(--purple);display:flex;align-items:center;justify-content:center}
.chat .count{position:absolute;right:-2px;top:-2px;width:14px;height:14px;border-radius:50%;background:#e23a2a;color:var(--white);font-size:9px;display:flex;align-items:center;justify-content:center}
</style>
</head>
<body>

<!-- header -->
<div class="abs brand header-brand"><span class="dot"></span>Floravine Pte Ltd</div>
<div class="abs badge header-badge"></div>
<nav class="abs nav"><a>Home</a><a>Services</a><a>Gallery</a><a>Calculator</a><a>Our portfolio</a><a>Testimonials</a><a>Contact</a><a>Blog</a></nav>
<div class="abs login"><span class="ico"><svg width="16" height="16" viewBox="0 0 16 16" fill="none" stroke="#fff" stroke-width="1.5"><circle cx="8" cy="5" r="3"/><path d="M2.5 14c.8-3 3-4.5 5.5-4.5s4.7 1.5 5.5 4.5"/></svg></span>Login</div>

<!-- hero -->
<div class="abs photo hero-left" role="img" aria-label="Open-plan office interior with exposed ceiling ducts"></div>
<div class="abs photo hero-right" role="img" aria-label="Dark glass-walled office corridor with pendant lights"></div>
<div class="abs hero-kicker">Floravine Pte Ltd</div>
<h1 class="abs hero-title">Interior<br>designer.</h1>
<div class="abs side-line"></div>
<div class="abs side-label">CONTACT US</div>
<a class="abs btn hero-btn">Get Started</a>
<div class="abs play"><span class="circle"><svg width="14" height="14" viewBox="0 0 14 14"><path d="M4 2l8 5-8 5z" fill="#fff"/></svg></span>Play Video</div>

<!-- partners -->
<svg class="abs partners" viewBox="0 0 1200 90" aria-label="Partner badges">
  <path d="M63 36l-7 8 7 8" fill="none" stroke="#6B429C" stroke-width="2.5"/>
  <path d="M1137 38l6 6-6 6" fill="none" stroke="#b9b4be" stroke-width="2"/>
  <rect x="97" y="10" width="174" height="78" rx="4" fill="#f1f1f1"/>
  <rect x="124" y="28" width="120" height="40" rx="8" fill="#dedede"/>
  <circle cx="362" cy="34" r="22" fill="#e1e1e1"/><rect x="312" y="62" width="100" height="12" rx="6" fill="#e8e8e8"/>
  <circle cx="515" cy="28" r="25" fill="#dcdcdc"/><rect x="485" y="58" width="60" height="12" rx="6" fill="#e3e3e3"/>
  <circle cx="648" cy="36" r="26" fill="#dcdcdc"/><rect x="670" y="20" width="72" height="32" rx="10" fill="#e3e3e3"/>
  <circle cx="836" cy="30" r="14" fill="#dcdcdc"/><rect x="852" y="22" width="104" height="28" rx="8" fill="#e6e6e6"/>
  <circle cx="1050" cy="40" r="36" fill="none" stroke="#dcdcdc" stroke-width="6"/><circle cx="1050" cy="40" r="14" fill="#d6d6d6"/>
</svg>

<!-- about -->
<div class="abs photo about-back" role="img" aria-label="Bright open office with white desks and grey chairs"></div>
<div class="abs about-front"><div role="img" aria-label="Glass-walled meeting rooms with timber floor"></div></div>
<h2 class="abs about-title">About Us</h2>
<p class="abs about-text">Lorem ipsum dolor sit amet, consectetur adipiscing elit, sed do eiusmod tempor incididunt ut labore et dolore magna aliqua. Quis ipsum suspendisse ultrices gravida. Risus commodo viverra maecenas accumsan lacus vel facilisis. Lorem ipsum dolor sit amet, consectetur adipiscing elit, sed do eiusmod tempor incididunt ut labore et dolore magna aliqua. Quis ipsum suspendisse ultrices gravida. Risus commodo viverra maecenas accumsan lacus vel facilisis.</p>
<a class="abs btn about-btn">Learn More</a>

<!-- gallery -->
<div class="abs gallery-band"></div>
<h2 class="abs section-title" style="top:1592px">Our Gallery</h2>
<div class="abs tile" style="left:112px;top:1681px;width:229px;height:225px;background:linear-gradient(90deg,#d8d2c8,#b9a98e 60%,#e6e1d8)" role="img" aria-label="Cafe counter with typographic wall and bar stools"></div>
<div class="abs tile tile-overlay" style="left:360px;top:1681px;width:230px;height:225px">Meranti Arc<br>Holdings</div>
<div class="abs tile" style="left:607px;top:1681px;width:480px;height:225px;background:linear-gradient(90deg,#4b5a33,#6d7f45 45%,#a6a98a 80%,#d5d3c8)" role="img" aria-label="Living green wall of potted plants"></div>
<div class="abs tile" style="left:112px;top:1928px;width:478px;height:226px;background:linear-gradient(90deg,#2f3a1f,#5c6c34 40%,#b38c61 75%,#d9c3a2)" role="img" aria-label="Indoor plants beside a lounge armchair"></div>
<div class="abs tile" style="left:607px;top:1928px;width:231px;height:226px;background:linear-gradient(180deg,#e7e3dc,#c8b89a 55%,#b68a48)" role="img" aria-label="Timber staircase with lit steps"></div>
<div class="abs tile" style="left:856px;top:1928px;width:231px;height:226px;background:linear-gradient(90deg,#a9b23d,#c7cfc8 40%,#8a8f92)" role="img" aria-label="Glass meeting room with lime accent wall"></div>

<!-- promo -->
<div class="abs promo-bg" role="img" aria-label="Warm yellow-tinted office interior"></div>
<svg class="abs" style="left:110px;top:2330px" width="580" height="495" viewBox="0 0 580 495">
  <defs><linearGradient id="wallGreen" x1="0" y1="0" x2="1" y2="1"><stop offset="0" stop-color="#3d5a27"/><stop offset=".55" stop-color="#61773a"/><stop offset="1" stop-color="#b89a6c"/></linearGradient></defs>
  <polygon points="8,8 576,8 400,490 8,490" fill="#fff"/>
  <polygon points="15,15 566,15 395,480 15,480" fill="url(#wallGreen)" role="img" aria-label="Office desks in front of a living green wall"/>
</svg>
<p class="abs promo-text">Bring goods straight from factory and cut away the middleman costing so client can have a better quality with affordable price.</p>
<a class="abs promo-link">Learn More</a>

<!-- awards -->
<h2 class="abs section-title" style="top:2982px">Awards</h2>
<svg class="abs" style="left:50px;top:3147px" width="20" height="24"><path d="M14 4l-8 8 8 8" fill="none" stroke="#6B429C" stroke-width="2.5"/></svg>
<svg class="abs" style="left:1130px;top:3147px" width="20" height="24"><path d="M6 4l8 8-8 8" fill="none" stroke="#b9b4be" stroke-width="2"/></svg>
<div class="abs award" style="left:118px;top:3085px;width:220px;height:150px"><span class="mark"></span></div>
<div class="abs award gold" style="left:368px;top:3085px;width:220px;height:150px"><span class="mark"></span></div>
<div class="abs award" style="left:610px;top:3085px;width:221px;height:150px"><span class="mark"></span></div>
<div class="abs award" style="left:856px;top:3085px;width:222px;height:150px"><span class="mark"></span></div>

<!-- footer -->
<div class="abs brand footer-brand"><span class="dot"></span>Floravine Pte Ltd</div>
<div class="abs badge footer-badge"></div>
<nav class="abs footer-nav"><a>Home</a><a>Services</a><a>Gallery</a><a>Calculator</a><a>Our portfolio</a><a>Testimonials</a><a>Contact</a><a>Blog</a></nav>
<p class="abs copy">Copyright© 2023 <span>Interior designer</span> | All rights reserved</p>
<div class="abs social on" style="left:500px;top:3665px"></div>
<div class="abs social" style="left:552px;top:3665px"></div>
<div class="abs social" style="left:604px;top:3665px"></div>
<div class="abs social" style="left:656px;top:3665px"></div>
<div class="abs chat"><svg width="22" height="20" viewBox="0 0 22 20" fill="#fff"><path d="M2 3h12v8H6l-4 3z"/><path d="M16 7h4v8l-3-2h-7v-1h6z"/></svg><span class="count">1</span></div>

</body>
</html>
```